RUVO WARE LTD

Advertisement to get more schools:
use website https://www.ruvo-ware.co.uk for logos etc.
ICT Service Level Agreements for as little as £2000 per year
Unlimited Remote, phone and email support
Unlimited Call outs included
90% fix time within 30 minutes of ticket submission
Extra support during Scolvar inspections
GDPR service included

Education

```html
<!DOCTYPE html>
<html lang="en">
<head>
<meta charset="utf-8">
<title>Ruvo Ware – Education Support &amp; Installation Banners</title>
<link href="https://fonts.googleapis.com/css2?family=Lato:wght@400;700&family=Righteous&display=swap" rel="stylesheet">
<style>
:root{
  --blue:#0a6fb8;
  --orange:#f4804b;
  --ink:#1d1d1b;
  --grey:#6b6b6b;
  --stage:#a7a7a7;
  --strip:#e6eef7;
  --white:#ffffff;
}
*{box-sizing:border-box;margin:0;padding:0}
html,body{width:1200px;height:2174px;overflow:hidden}
body{background:var(--stage);font-family:'Lato',sans-serif;color:var(--ink);position:relative}
.banner{position:absolute;top:107px;width:463px;background:var(--white);overflow:hidden}
.banner--features{left:116px;height:1813px}
.banner--services{left:622px;height:1960px}
.abs{position:absolute}

/* brand lockup */
.brand{position:absolute;display:flex;flex-direction:column;align-items:center}
.brand__name{display:flex;align-items:center;gap:7px;font-family:'Lato',sans-serif;font-weight:700;font-size:25px;letter-spacing:1px;color:var(--blue);line-height:1;white-space:nowrap}
.brand__mark{width:16px;height:16px;background:var(--orange)}
.brand__tag{font-size:8px;letter-spacing:1px;color:var(--blue);margin-top:6px;white-space:nowrap}
.banner .brand--top{top:16px;left:0;width:100%}
.brand--light .brand__name,.brand--light .brand__tag{color:var(--white)}
.brand--footer .brand__name{font-size:21px}
.brand--footer .brand__mark{width:14px;height:14px}
.brand--footer .brand__tag{font-size:7.5px}

/* hero */
.hero-band{left:0;top:66px;width:463px;height:338px;background:var(--blue);border-radius:0 0 70px 70px}
.hero-photo{left:0;top:66px;width:449px;height:322px;border-radius:0 0 56px 56px;border:3px solid var(--white);border-top:none;
  background:linear-gradient(160deg,#8fa97a 0%,#c9b9a2 30%,#3c4a5c 60%,#6d6a66 100%)}

/* headings */
.title{font-family:'Righteous',sans-serif;line-height:1.2;text-transform:uppercase;white-space:nowrap}
.title__blue{color:var(--blue);display:block}
.title__orange{color:var(--orange);display:block}

/* left banner features */
.banner--features .title{left:32px;top:472px;font-size:38px}
.feature-list{left:32px;top:598px;list-style:none}
.feature{display:flex;align-items:center;height:62px;margin-bottom:40px}
.feature__icon{width:67px;height:62px;border-radius:3px;display:flex;align-items:center;justify-content:center;flex:none}
.feature__icon--blue{background:var(--blue)}
.feature__icon--orange{background:var(--orange)}
.feature__text{margin-left:22px;font-size:20px;line-height:27px;width:300px}
.photo-fade{left:0;top:1171px;width:463px;height:378px;
  background:linear-gradient(180deg,#ffffff 0%,#c7d7e2 25%,#9a8572 60%,#b38a5a 100%)}
.footer--blue{left:0;top:1549px;width:463px;height:264px;background:var(--blue);color:var(--white)}
.contact{position:absolute;left:32px;font-size:13.5px;font-weight:700;line-height:21.5px;list-style:none}
.contact li{display:flex;gap:13px;white-space:nowrap}
.contact svg{flex:none;margin-top:4px}
.contact .indent{padding-left:27px}
.footer--blue .contact{top:63px}
.footer--blue .brand{left:282px;top:64px}
.copyright{position:absolute;left:0;width:100%;text-align:center;font-size:13px}
.footer--blue .copyright{top:218px}

/* right banner */
.banner--services .title{left:40px;top:448px;font-size:36px}
.bullets{left:40px;top:552px;list-style:none;font-size:15px}
.bullets li{display:flex;align-items:center;height:30.7px}
.bullets li::before{content:"";width:14px;height:14px;border-radius:50%;background:var(--orange);margin:0 24px 0 0;flex:none}
.tile{position:absolute;color:var(--white);font-size:11px;line-height:19px;text-align:center;padding:34px 6px 0;border-radius:0 0 3px 3px}
.tile--blue{background:var(--blue)}
.tile--orange{background:var(--orange)}
.tile__badge{position:absolute;left:50%;top:-16px;margin-left:-17px;width:34px;height:34px;border-radius:50%;background:var(--orange);border:2px solid var(--white);display:flex;align-items:center;justify-content:center}
.photo-about{left:5px;top:1102px;width:453px;height:274px;border-radius:0 0 6px 6px;
  background:linear-gradient(120deg,#7d8fa6 0%,#cfd6de 40%,#9aa4ad 70%,#6f7b86 100%)}
.about{left:31px;top:1338px;width:402px;height:60px;background:var(--white)}
.about-title{left:0;top:1366px;width:100%;text-align:center;font-family:'Righteous',sans-serif;font-size:30px;text-transform:uppercase}
.about-title .blue{color:var(--blue)}
.about-title .orange{color:var(--orange)}
.about-copy{left:30px;top:1417px;width:403px;text-align:center;font-size:12.5px;line-height:21.5px;color:var(--grey)}
.apply{left:176px;top:1572px;width:111px;height:41px;background:var(--orange);color:var(--white);font-size:13px;font-weight:700;display:flex;align-items:center;justify-content:center;border-radius:2px}
.partners{left:0;top:1655px;width:463px;height:76px;background:var(--strip);display:flex;align-items:center;justify-content:center;gap:14px}
.partner{height:34px;border-radius:4px;background:#c3cfdc}
.partner--round{border-radius:17px;background:#2e7d6b}
.partner--green{background:#8cc63f}
.footer--light .contact{top:1773px;color:var(--ink)}
.footer--light .brand{left:282px;top:1774px}
.divider{left:0;top:1898px;width:463px;height:1px;background:#dcdcdc}
.footer--light .copyright{top:1921px;color:var(--ink)}
</style>
</head>
<body>

<!-- Feature roll-up -->
<section class="banner banner--features">
  <div class="brand brand--top">
    <div class="brand__name"><span class="brand__mark"></span>RUVO WARE</div>
    <div class="brand__tag">EDUCATION SUPPORT &amp; INSTALLATION</div>
  </div>
  <div class="abs hero-band"></div>
  <div class="abs hero-photo" role="img" aria-label="Pupils in school uniform working at computers in a classroom"></div>

  <h1 class="abs title"><span class="title__blue">Education Support</span><span class="title__orange">&amp; Installation</span></h1>

  <ul class="abs feature-list">
    <li class="feature"><span class="feature__icon feature__icon--blue">
      <svg width="30" height="30" viewBox="0 0 30 30" fill="none" stroke="#fff" stroke-width="3"><rect x="3" y="6" width="24" height="21" rx="2"/><line x1="3" y1="12" x2="27" y2="12"/><line x1="9" y1="2" x2="9" y2="8"/><line x1="21" y1="2" x2="21" y2="8"/></svg>
    </span><span class="feature__text">ICT SLA agreements for as<br>little as £2000 per year</span></li>
    <li class="feature"><span class="feature__icon feature__icon--orange">
      <svg width="34" height="30" viewBox="0 0 34 30" fill="#fff"><circle cx="12" cy="16" r="9"/><circle cx="12" cy="16" r="3.5" fill="#f4804b"/><circle cx="26" cy="8" r="5"/><circle cx="26" cy="8" r="2" fill="#f4804b"/><circle cx="26" cy="23" r="5"/><circle cx="26" cy="23" r="2" fill="#f4804b"/></svg>
    </span><span class="feature__text">Unlimited Remote, phone<br>and email support</span></li>
    <li class="feature"><span class="feature__icon feature__icon--blue">
      <svg width="30" height="30" viewBox="0 0 24 24" fill="#fff"><path d="M20 15.5c-1.2 0-2.4-.2-3.6-.6-.3-.1-.7 0-1 .2l-2.2 2.2c-2.8-1.4-5.1-3.8-6.6-6.6l2.2-2.2c.3-.3.4-.7.2-1-.3-1.1-.5-2.3-.5-3.5 0-.6-.4-1-1-1H4c-.6 0-1 .4-1 1 0 9.4 7.6 17 17 17 .6 0 1-.4 1-1v-3.5c0-.6-.4-1-1-1z" transform="scale(-1,1) translate(-24,0)"/></svg>
    </span><span class="feature__text">Unlimited Call outs included</span></li>
    <li class="feature"><span class="feature__icon feature__icon--orange">
      <svg width="30" height="30" viewBox="0 0 30 30"><circle cx="15" cy="15" r="13" fill="#fff"/><path d="M15 7v9l5 3" stroke="#f4804b" stroke-width="3" fill="none" stroke-linecap="round"/></svg>
    </span><span class="feature__text">90% fix time within 30 minutes<br>of ticket submission</span></li>
    <li class="feature"><span class="feature__icon feature__icon--blue">
      <svg width="30" height="30" viewBox="0 0 30 30" fill="none" stroke="#fff" stroke-width="4"><circle cx="12" cy="12" r="8"/><line x1="18" y1="18" x2="27" y2="27" stroke-linecap="round"/></svg>
    </span><span class="feature__text">Extra support during Scolvar<br>inspections</span></li>
    <li class="feature"><span class="feature__icon feature__icon--orange">
      <svg width="26" height="32" viewBox="0 0 26 32" fill="#fff"><path d="M2 0h15l9 9v23H2z"/><path d="M17 0v9h9z" fill="#f9b08e"/></svg>
    </span><span class="feature__text">GDPR service included</span></li>
  </ul>

  <div class="abs photo-fade" role="img" aria-label="Girl using a laptop and building a robotics kit in class"></div>

  <footer class="abs footer--blue">
    <ul class="contact">
      <li><svg width="14" height="12" viewBox="0 0 14 12" fill="#f4804b"><path d="M0 2l4-2 5 2 5-2v10l-5 2-5-2-4 2z"/></svg>Ruvo Ware LTD Halden House,</li>
      <li class="indent">Mercer Street</li>
      <li class="indent">Ashby Lancashire AB9 4XY</li>
      <li><svg width="14" height="14" viewBox="0 0 24 24" fill="#f4804b"><path d="M4 15.5c1.2 0 2.4-.2 3.6-.6.3-.1.7 0 1 .2l2.2 2.2c2.8-1.4 5.1-3.8 6.6-6.6l-2.2-2.2c-.3-.3-.4-.7-.2-1 .3-1.1.5-2.3.5-3.5 0-.6.4-1 1-1H20c.6 0 1 .4 1 1 0 9.4-7.6 17-17 17-.6 0-1-.4-1-1v-3.5c0-.6.4-1 1-1z"/></svg>0161 555 0142</li>
      <li><svg width="14" height="12" viewBox="0 0 14 12" fill="#f4804b"><path d="M0 0h14v2L7 6 0 2zM0 4l7 4 7-4v8H0z"/></svg>info@ruvo-ware.co.uk</li>
    </ul>
    <div class="brand brand--light brand--footer">
      <div class="brand__name"><span class="brand__mark"></span>RUVO WARE</div>
      <div class="brand__tag">EDUCATION SUPPORT &amp; INSTALLATION</div>
    </div>
    <p class="copyright">Copyrights © 2022 Ruvo Ware. All rights Reserved &nbsp;|&nbsp; Privacy</p>
  </footer>
</section>

<!-- Services roll-up -->
<section class="banner banner--services">
  <div class="brand brand--top">
    <div class="brand__name"><span class="brand__mark"></span>RUVO WARE</div>
    <div class="brand__tag">EDUCATION SUPPORT &amp; INSTALLATION</div>
  </div>
  <div class="abs hero-band"></div>
  <div class="abs hero-photo" role="img" aria-label="Pupils in school uniform working at computers in a classroom"></div>

  <h1 class="abs title"><span class="title__blue">Education Support</span><span class="title__orange">&amp; Installation</span></h1>

  <ul class="abs bullets">
    <li>ICT SLA agreements for as little as £2000 per year</li>
    <li>Unlimited Remote, phone and email support</li>
    <li>Unlimited Call outs included</li>
    <li>90% fix time within 30 minutes of ticket submission</li>
    <li>Extra support during Scolvar inspections</li>
    <li>GDPR service included</li>
  </ul>

  <div class="tile tile--blue" style="left:0;top:787px;width:149px;height:144px"><span class="tile__badge"><svg width="18" height="18" viewBox="0 0 18 18" fill="none" stroke="#fff" stroke-width="1.6"><circle cx="9" cy="9" r="7"/><circle cx="9" cy="9" r="3"/></svg></span>Ruvo Ware provides managed support contracts to accommodate the individual needs of a school</div>
  <div class="tile tile--orange" style="left:155px;top:787px;width:152px;height:144px"><span class="tile__badge"><svg width="18" height="18" viewBox="0 0 18 18" fill="none" stroke="#fff" stroke-width="1.6"><rect x="3" y="2" width="12" height="14" rx="1"/><line x1="3" y1="7" x2="15" y2="7"/><line x1="3" y1="11" x2="15" y2="11"/></svg></span>We supply and install everything from Laptops, PCs, Printers, Servers, Tablets</div>
  <div class="tile tile--blue" style="left:313px;top:787px;width:150px;height:144px"><span class="tile__badge"><svg width="18" height="18" viewBox="0 0 18 18" fill="none" stroke="#fff" stroke-width="1.6"><path d="M5 14a4 4 0 010-8 5 5 0 019 1 3.5 3.5 0 010 7z"/></svg></span>We have a complete range of hosting services including Email hosting, Website hosting, Blogs</div>
  <div class="tile tile--blue" style="left:0;top:952px;width:149px;height:137px"><span class="tile__badge"><svg width="18" height="18" viewBox="0 0 24 24" fill="#fff"><path d="M20 15.5c-1.2 0-2.4-.2-3.6-.6-.3-.1-.7 0-1 .2l-2.2 2.2c-2.8-1.4-5.1-3.8-6.6-6.6l2.2-2.2c.3-.3.4-.7.2-1-.3-1.1-.5-2.3-.5-3.5 0-.6-.4-1-1-1H4c-.6 0-1 .4-1 1 0 9.4 7.6 17 17 17 .6 0 1-.4 1-1v-3.5c0-.6-.4-1-1-1z"/></svg></span>We offer fast, flexible, reliable and cost-effective business phone lines, SIP Trunking and mobile.</div>
  <div class="tile tile--orange" style="left:155px;top:952px;width:152px;height:137px"><span class="tile__badge"><svg width="18" height="18" viewBox="0 0 18 18" fill="none" stroke="#fff" stroke-width="1.4"><circle cx="9" cy="9" r="7"/><ellipse cx="9" cy="9" rx="3" ry="7"/><line x1="2" y1="9" x2="16" y2="9"/></svg></span>Choose exactly the right business-grade broadband package for your education needs.</div>
  <div class="tile tile--blue" style="left:313px;top:952px;width:150px;height:137px"><span class="tile__badge"><svg width="18" height="18" viewBox="0 0 18 18" fill="none" stroke="#fff" stroke-width="1.6"><rect x="4" y="8" width="10" height="8" rx="1"/><path d="M6 8V5a3 3 0 016 0v3"/></svg></span>Ruvo Ware is partnered with Norvane, providing the most cost effective protection for your organisation.</div>

  <div class="abs photo-about" role="img" aria-label="Pupils working on laptops in a bright classroom"></div>
  <div class="abs about"></div>
  <h2 class="abs about-title"><span class="blue">About</span> <span class="orange">Us</span></h2>
  <p class="abs about-copy">Ruvo Ware, is a registered UK Limited Company<br>Our goal is to provide comprehensive ICT support along with excellent customer service to the education sector.<br>We offer support in all aspects of ICT in education, from technical faults to assisting teachers and coordinators to meet the requirements of the computing curriculum</p>
  <div class="abs apply">APPLY NOW</div>

  <div class="abs partners" aria-label="Partner badges">
    <span class="partner" style="width:92px"></span>
    <span class="partner" style="width:100px"></span>
    <span class="partner partner--round" style="width:92px"></span>
    <span class="partner partner--green" style="width:96px"></span>
  </div>

  <footer class="footer--light">
    <ul class="contact">
      <li><svg width="14" height="12" viewBox="0 0 14 12" fill="#0a6fb8"><path d="M0 2l4-2 5 2 5-2v10l-5 2-5-2-4 2z"/></svg>Ruvo Ware LTD Halden House,</li>
      <li class="indent">Mercer Street</li>
      <li class="indent">Ashby Lancashire AB9 4XY</li>
      <li><svg width="14" height="14" viewBox="0 0 24 24" fill="#0a6fb8"><path d="M4 15.5c1.2 0 2.4-.2 3.6-.6.3-.1.7 0 1 .2l2.2 2.2c2.8-1.4 5.1-3.8 6.6-6.6l-2.2-2.2c-.3-.3-.4-.7-.2-1 .3-1.1.5-2.3.5-3.5 0-.6.4-1 1-1H20c.6 0 1 .4 1 1 0 9.4-7.6 17-17 17-.6 0-1-.4-1-1v-3.5c0-.6.4-1 1-1z"/></svg>0161 555 0142</li>
      <li><svg width="14" height="12" viewBox="0 0 14 12" fill="#0a6fb8"><path d="M0 0h14v2L7 6 0 2zM0 4l7 4 7-4v8H0z"/></svg>info@ruvo-ware.co.uk</li>
    </ul>
    <div class="brand brand--footer">
      <div class="brand__name"><span class="brand__mark"></span>RUVO WARE</div>
      <div class="brand__tag">EDUCATION SUPPORT &amp; INSTALLATION</div>
    </div>
    <div class="abs divider"></div>
    <p class="copyright">Copyrights © 2022 Ruvo Ware. All rights Reserved &nbsp;|&nbsp; Privacy</p>
  </footer>
</section>

</body>
</html>
```